Laser Tattoo Removal Business Cards

We are looking for a professional business card design for a laser tattoo removal business. Ideally looking for a black business card design. The name of the business is Brightline Tattoo Removal. We place our cards at local tattoo shops so we ideally are looking for something trendy/edgy to draw both male and female clientele in.

Target Market(s)

Male/Female ages 18-60

Contact Information for Business Card

black background ideally.. hoping to stay within greys, whites and black

Font styles to use
Serif
Sans Serif

Colors
121212
a9a9a9
5c5c5c
f5f5f5
ffffff
7f7f7f
606060
848484
9d9d9d

Requirements
Must have
• Employee Info:
• Melissa Thornbury
• Chief Executive Offer
• m: 919.537.2846
• w: 919.362.4178
• f: 919.685.3907
• mthornbury@brightlinetattooremoval.example
• Address:
• 4615 Oakmere Pkwy, Suite 210
• Raleigh, NC 27654
• Website:
• www.brightlinetattooremoval.example
Nice to have
• Myabe business name on back or logo on back and employee info on the front

```html
<!DOCTYPE html>
<html lang="en">
<head>
<meta charset="utf-8">
<title>Brightline Tattoo Removal – Business Cards</title>
<link rel="stylesheet" href="https://fonts.googleapis.com/css2?family=Oswald:wght@400;500&family=Montserrat:wght@400;600&display=swap">
<style>
  :root {
    --ink: #121212;
    --card-dark: #1b1b1d;
    --white: #ffffff;
    --paper: #ffffff;
    --grey-light: #a9a9a9;
    --grey-mid: #848484;
    --grey-dark: #5c5c5c;
    --text-contact: #4a4a4a;
    --bg-left: #d4d4d4;
    --bg-right: #858585;
  }
  * { margin: 0; padding: 0; box-sizing: border-box; }
  html, body { width: 1200px; height: 960px; overflow: hidden; }
  body {
    position: relative;
    background: linear-gradient(90deg, var(--bg-left), var(--bg-right));
    font-family: "Montserrat", Arial, sans-serif;
  }

  /* Front card */
  .card-front {
    position: absolute;
    left: 302px; top: 122px;
    width: 600px; height: 343px;
    background: var(--paper);
  }
  .logo-tab {
    position: absolute;
    left: 36px; top: 0;
    width: 127px; height: 133px;
    background: var(--ink);
    clip-path: polygon(0 0, 100% 0, 100% 100%, 18px 100%, 0 115px);
    display: flex; flex-direction: column; align-items: center; justify-content: center;
    padding-top: 18px;
  }
  .logo-name {
    font-family: "Oswald", "Arial Narrow", sans-serif;
    font-weight: 400;
    color: var(--white);
    text-transform: uppercase;
    text-align: center;
    line-height: 1.1;
  }
  .logo-tab .logo-name .line-main { display: block; font-size: 19px; letter-spacing: 1px; }
  .logo-tab .logo-name .line-sub { display: block; font-size: 8.5px; letter-spacing: 1.5px; margin-top: 6px; }

  .person {
    position: absolute;
    left: 180px; top: 80px;
  }
  .person-name {
    font-family: "Oswald", "Arial Narrow", sans-serif;
    font-weight: 400;
    font-size: 36px;
    line-height: 1;
    color: var(--ink);
    text-transform: uppercase;
    transform: scaleX(0.82);
    transform-origin: left center;
    white-space: nowrap;
  }
  .person-title {
    font-family: "Oswald", "Arial Narrow", sans-serif;
    font-weight: 500;
    font-size: 14px;
    color: var(--grey-light);
    text-transform: uppercase;
    letter-spacing: 0.4px;
    margin-top: 2px;
  }

  .contact {
    position: absolute;
    right: 34px; top: 188px;
    text-align: right;
    font-size: 13.5px;
    line-height: 18px;
    color: var(--text-contact);
  }
  .contact .address { margin-bottom: 4px; }
  .contact .web strong { font-weight: 600; color: var(--ink); }

  /* Back card */
  .card-back {
    position: absolute;
    left: 299px; top: 495px;
    width: 600px; height: 343px;
    background: var(--card-dark);
  }
  .card-back .frame {
    position: absolute;
    inset: 9px;
    border: 1px solid var(--grey-dark);
  }
  .card-back .logo-name {
    position: absolute;
    left: 0; right: 0; top: 108px;
    color: #e6e6e6;
  }
  .card-back .logo-name .line-main { display: block; font-size: 50px; letter-spacing: 4px; }
  .card-back .logo-name .line-sub { display: block; font-size: 20px; letter-spacing: 5px; margin-top: 40px; }
</style>
</head>
<body>
  <section class="card-front">
    <div class="logo-tab">
      <p class="logo-name"><span class="line-main">Brightline</span><span class="line-sub">Tattoo Removal</span></p>
    </div>
    <div class="person">
      <h1 class="person-name">Melissa Thornbury</h1>
      <p class="person-title">Chief Executive Offer</p>
    </div>
    <div class="contact">
      <p class="address">4615 Oakmere Pkwy, Suite 210<br>Raleigh, NC 27654</p>
      <p>M: 919.537.2846</p>
      <p>W: 919.362.4178</p>
      <p>F: 919.685.3907</p>
      <p>mthornbury@brightlinetattooremoval.example</p>
      <p class="web">www.<strong>brightlinetattooremoval</strong>.example</p>
    </div>
  </section>

  <section class="card-back">
    <div class="frame"></div>
    <p class="logo-name"><span class="line-main">Brightline</span><span class="line-sub">Tattoo Removal</span></p>
  </section>
</body>
</html>
```